Stationary Set Rebrand for Brennick

We are a Canadian Distribution and Service Company that was established in 1969. Over the past 5 decades we have expanded our business and have warehouses across Canada. We specialize in adhesive tapes, adhesives, films, safety, warehouse, shipping, janitorial and packaging supplies.

We have updated our logo design and would like a new corporate branding identity that includes a new fresh Stationary Set (Business Cards, Letterhead, Letterhead MS Word, Envelope, Presentation Folders, Email Signatures, Notepad Covers, etc.)

Target Market(s)

Industrial Business Sector

Font styles to use
Sans Serif

Colors
0054AA
0677BA
7BADD7
CADEEF
E8F1F8
0094D4
00A9DD
6FCCEA
C7EBF8
E9F6FB
00AB8E
00BBA5
67D7C9
C6EFE9
E9F9F6
EB3D1F
EC4F4E
F09395
F8D3D4
FCEDEE

Requirements
Should not have
• Colors not too light, darker colours preferred

```html
<!DOCTYPE html>
<html lang="en">
<head>
<meta charset="utf-8">
<title>Brennick Stationery Set</title>
<link href="https://fonts.googleapis.com/css2?family=Poppins:wght@400;500;700&family=Open+Sans:wght@400;600;700&display=swap" rel="stylesheet">
<style>
:root{
  --red:#dc1a22;
  --red-dark:#b8141b;
  --ink:#111214;
  --paper:#ffffff;
  --stage:#d8dde0;
  --folder:#dfe1e3;
  --grey-text:#333;
}
*{box-sizing:border-box;margin:0;padding:0}
html,body{width:1200px;height:684px;overflow:hidden;background:var(--stage)}
body{position:relative;font-family:"Poppins",sans-serif;color:var(--ink)}
.piece{position:absolute;background:var(--paper);box-shadow:0 3px 8px rgba(0,0,0,.15);overflow:hidden}
.edge{position:absolute;left:0;top:0;bottom:0;width:9px;background:var(--red);border-right:2px solid var(--ink)}
.wordmark{position:absolute;font-family:"Poppins",sans-serif;font-weight:700;color:var(--ink);letter-spacing:-.5px;line-height:1}
.contact{position:absolute;font-family:"Poppins",sans-serif;line-height:1.35}
.contact .row{display:flex;align-items:center;gap:4px}
.icon{width:1em;height:1em;flex:none;fill:var(--red)}
.red{color:var(--red)}

/* envelope */
.envelope-front{left:50px;top:53px;width:270px;height:120px}
.envelope-front .wordmark{left:16px;top:10px;font-size:19px}
.envelope-front .contact{left:16px;top:77px;font-size:5.2px;color:var(--grey-text)}
.envelope-front .gap{height:5px}
.envelope-back{left:51px;top:187px;width:269px;height:119px}
.envelope-back .flap{position:absolute;left:0;top:0;width:100%;height:40px;border-bottom:1px solid #e6e6e6;border-radius:0 0 10px 10px;box-shadow:0 4px 6px rgba(0,0,0,.08)}
.envelope-back .seal{position:absolute;left:129px;top:12px;width:10px;height:10px;border-radius:50%;background:var(--red)}

/* business cards */
.card{border-radius:10px}
.card-front{left:51px;top:316px;width:264px;height:152px}
.card-front .wordmark{left:0;right:0;top:52px;text-align:center;font-size:40px}
.card-front .tagline{position:absolute;left:0;right:0;top:98px;text-align:center;font-size:8px;font-weight:500}
.card-back{left:51px;top:483px;width:264px;height:151px}
.divider{position:absolute;width:1px;background:var(--red)}
.card-back .wordmark{left:12px;top:64px;font-size:22px}
.card-back .divider{left:131px;top:30px;height:92px}
.person .name{font-size:15px;font-weight:400;line-height:1.1;white-space:nowrap}
.person .name b{font-weight:500;color:var(--red)}
.person .role{font-size:7px;font-weight:500;margin-bottom:7px}
.person .addr{font-size:7.5px;margin-bottom:6px}
.person .row{font-size:7.5px}
.card-back .person{position:absolute;left:151px;top:20px}

/* letterhead */
.letterhead{left:354px;top:55px;width:318px;height:449px}
.letterhead .edge{width:15px}
.letterhead .wordmark{left:28px;top:30px;font-size:24px}
.letterhead .tagline{position:absolute;left:28px;top:56px;font-size:5px;font-weight:500}
.letterhead .head-contact{position:absolute;right:16px;top:17px;text-align:right;font-size:6.6px;line-height:1.3}
.letterhead .head-contact .row{justify-content:flex-end}
.letterhead .head-contact .gap{height:5px}
.letterhead .rule{position:absolute;left:17px;top:69px;width:195px;height:1px;background:var(--ink)}
.letterhead .rule-red{position:absolute;left:196px;top:68px;width:105px;height:2px;background:var(--red)}
.letter{position:absolute;left:34px;top:105px;width:262px;font-family:"Open Sans",sans-serif;font-size:6.1px;line-height:1.38;color:#222}
.letter .date{margin-bottom:7px}
.letter .to{font-size:7.8px;font-weight:700;color:var(--ink);line-height:1.1}
.letter .addr{margin:4px 0 14px}
.letter p{text-align:justify;margin-bottom:8px}
.signature{width:85px;height:22px;margin-top:4px;background:linear-gradient(90deg,rgba(17,18,20,.12),rgba(17,18,20,.04));border-radius:3px}
.letter .signer{font-size:13.5px;font-weight:700;color:var(--ink);line-height:1.1;margin-top:2px}

/* email signature */
.email-sig{left:354px;top:526px;width:318px;height:106px}
.email-sig .edge{width:9px}
.email-sig .wordmark{left:24px;top:36px;font-size:24px}
.email-sig .divider{left:158px;top:12px;height:80px}
.email-sig .person{position:absolute;left:186px;top:12px}
.email-sig .person .role{margin-bottom:5px}
.email-sig .person .addr{font-size:6.8px;margin-bottom:4px}
.email-sig .person .row{font-size:6.8px}
.socials{position:absolute;left:340px;top:97px;display:flex;gap:4px}
.socials span{width:5px;height:5px;border-radius:50%;background:var(--red)}
.email-sig .socials{left:140px}

/* folder */
.folder-front{left:696px;top:53px;width:139px;height:270px;background:linear-gradient(135deg,#eceef0,#cfd2d5)}
.folder-front .edge{width:6px;border-right-width:1px}
.folder-front .wordmark{right:10px;bottom:22px;font-size:17px}
.insert{left:836px;top:80px;width:37px;height:216px;font-size:3px;line-height:1.4;padding:8px 3px 0;color:#333}
.insert .band{position:absolute;left:0;right:0;bottom:0;height:70px;background:var(--red)}
.insert .line{margin-bottom:6px}
.folder-open{left:909px;top:68px;width:261px;height:243px;background:transparent;box-shadow:none}
.folder-open .left{position:absolute;left:0;top:0;width:130px;height:100%;background:linear-gradient(90deg,#fff,#eef0f1)}
.folder-open .right{position:absolute;left:130px;top:0;width:131px;height:100%;background:linear-gradient(135deg,#d6d9dc,#e9ebed)}
.folder-open svg{position:absolute;left:130px;top:0}

/* notebook */
.notebook{left:760px;top:392px;width:340px;height:218px;background:var(--ink);border-radius:3px}
.notebook .band{position:absolute;left:0;right:0;top:0;height:22px;background:var(--red)}
.notebook .spiral{position:absolute;left:10px;right:10px;top:4px;display:flex;justify-content:space-between}
.notebook .spiral span{width:7px;height:12px;border:2px solid #2a2a2a;border-radius:4px;background:var(--stage)}
.notebook .pattern{position:absolute;left:0;right:0;top:24px;bottom:0;background:linear-gradient(135deg,#1b1c1f 0%,#2c2d31 60%,#3a3b40 100%)}
.notebook .wordmark{left:20px;bottom:18px;font-size:26px;color:#9a9ca0}
</style>
</head>
<body>

<svg width="0" height="0" style="position:absolute">
  <defs>
    <symbol id="i-pin" viewBox="0 0 24 24"><path d="M12 2a7 7 0 0 0-7 7c0 5 7 13 7 13s7-8 7-13a7 7 0 0 0-7-7zm0 9.5A2.5 2.5 0 1 1 12 6.5a2.5 2.5 0 0 1 0 5z"/></symbol>
    <symbol id="i-phone" viewBox="0 0 24 24"><path d="M6.6 10.8a15 15 0 0 0 6.6 6.6l2.2-2.2a1 1 0 0 1 1-.25 11.4 11.4 0 0 0 3.6.57 1 1 0 0 1 1 1V20a1 1 0 0 1-1 1A17 17 0 0 1 3 4a1 1 0 0 1 1-1h3.5a1 1 0 0 1 1 1c0 1.25.2 2.45.57 3.57a1 1 0 0 1-.25 1z"/></symbol>
    <symbol id="i-mail" viewBox="0 0 24 24"><path d="M3 5h18v14H3zm2 2v.5l7 5 7-5V7z"/></symbol>
    <symbol id="i-web" viewBox="0 0 24 24"><path d="M12 2a10 10 0 1 0 0 20 10 10 0 0 0 0-20zm6.9 6h-3a15 15 0 0 0-1.3-3.9A8 8 0 0 1 18.9 8zM12 4c.9 1.2 1.6 2.5 2 4h-4c.4-1.5 1.1-2.8 2-4zM4.3 14a8 8 0 0 1 0-4h3.4a16 16 0 0 0 0 4zm.8 2h3a15 15 0 0 0 1.3 3.9A8 8 0 0 1 5.1 16zM8 8H5.1a8 8 0 0 1 4.3-3.9A15 15 0 0 0 8 8zm4 12c-.9-1.2-1.6-2.5-2-4h4c-.4 1.5-1.1 2.8-2 4zm2.3-6H9.7a14 14 0 0 1 0-4h4.6a14 14 0 0 1 0 4zm.3 5.9A15 15 0 0 0 16 16h3a8 8 0 0 1-4.4 3.9zM16.3 14a16 16 0 0 0 0-4h3.4a8 8 0 0 1 0 4z"/></symbol>
  </defs>
</svg>

<!-- Envelope front -->
<section class="piece envelope-front">
  <div class="edge"></div>
  <div class="wordmark">Brennick</div>
  <div class="contact">
    <div>418 Harbourline Rd. Suite 12</div>
    <div>Moncton, NB E1C 4B7</div>
    <div class="gap"></div>
    <div class="row"><svg class="icon"><use href="#i-phone"/></svg>(506) 555-0147</div>
    <div class="row"><svg class="icon"><use href="#i-mail"/></svg>hello@brennicksupply.ca</div>
    <div class="row"><svg class="icon"><use href="#i-web"/></svg>brennicksupply.ca</div>
  </div>
</section>

<!-- Envelope back -->
<section class="piece envelope-back">
  <div class="flap"></div>
  <div class="seal"></div>
</section>

<!-- Business card front -->
<section class="piece card card-front">
  <div class="edge"></div>
  <div class="wordmark">Brennick</div>
  <div class="tagline">Tape and Packaging Specialists</div>
</section>

<!-- Business card back -->
<section class="piece card card-back">
  <div class="edge"></div>
  <div class="wordmark">Brennick</div>
  <div class="divider"></div>
  <div class="person contact">
    <div class="name"><b>Mira</b> Calder</div>
    <div class="role">Founder &amp; CEO</div>
    <div class="addr">418 Harbourline Rd. Suite 12<br>Moncton, NB E1C 4B7</div>
    <div class="row"><svg class="icon"><use href="#i-phone"/></svg>(506) 555-0147</div>
    <div class="row"><svg class="icon"><use href="#i-mail"/></svg>info@brennicksupply.ca</div>
    <div class="row"><svg class="icon"><use href="#i-web"/></svg>www.brennicksupply.ca</div>
  </div>
</section>

<!-- Letterhead -->
<section class="piece letterhead">
  <div class="edge"></div>
  <div class="wordmark">Brennick</div>
  <div class="tagline">Tape and Packaging Specialists</div>
  <div class="head-contact">
    <div class="row">418 Harbourline Rd. Suite 12 <svg class="icon"><use href="#i-pin"/></svg></div>
    <div class="row">Moncton, NB E1C 4B7 <span style="width:1em"></span></div>
    <div class="gap"></div>
    <div class="row">(506) 555-0147 <svg class="icon"><use href="#i-phone"/></svg></div>
    <div class="row">info@brennicksupply.ca <svg class="icon"><use href="#i-mail"/></svg></div>
    <div class="row">www.brennicksupply.ca <svg class="icon"><use href="#i-web"/></svg></div>
  </div>
  <div class="rule"></div>
  <div class="rule-red"></div>
  <div class="letter">
    <div class="date">August-05-2019</div>
    <div class="to">Dana Whitlock</div>
    <div>Director</div>
    <div class="addr">418 Harbourline Rd. Suite 12<br>Moncton, NB E1C 4B7</div>
    <div class="to" style="margin-bottom:7px">Dana Whitlock</div>
    <p>Lorem ipsum dolor sit amet, consectetuer adipiscing elit, sed diam nonummy nibh euismod tincidunt ut laoreet dolore magna aliquam erat volutpat. Ut wisi enim ad minim veniam, quis nostrud exerci tation ullamcorper suscipit lobortis</p>
    <p>Lorem ipsum dolor sit amet, cons ectetuer adipiscing elit, sed diam nonummy nibh euismod tincidunt ut laoreet dolore magna aliquam erat volutpat. Ut wisi enim ad minim veniam, quis nostrud exerci tation ullamcorper suscipit lobortis nisl ut aliquip ex ea commodo consequat. Lorem ipsum dolor sit amet, consectetuer olutpat. Ut wisi enim ad minim veniam, quis nostrud exerci tation ullamcorper suscipit lobortis nisl ut aliquip ex ea commodo consequat. Duis autem</p>
    <p>vel eum iriure dolor in hendrerit in vulputate velit esse molestie consequat, vel illum dolore eu feugiat nulla facilisis at vero eros et accumsan et iusto odio dignissim qui blandit praesent luptatum zzril delenit augue duis dolore te feugait nulla facilisi. Lorem ipsum dolor sit amet, cons ectetuer adipiscing elit, sed diam nonummy nibh euismod tincidunt ut laoreet dolore magna aliquam erat volutpat. Ut wisi enim .</p>
    <div class="signature" role="img" aria-label="Handwritten signature of Rowan Keller"></div>
    <div class="signer">Rowan Keller</div>
    <div>Co-Founder</div>
  </div>
</section>

<!-- Email signature -->
<section class="piece email-sig">
  <div class="edge"></div>
  <div class="wordmark">Brennick</div>
  <div class="divider"></div>
  <div class="person contact">
    <div class="name"><b>Mira</b> Calder</div>
    <div class="role">Founder &amp; CEO</div>
    <div class="addr">418 Harbourline Rd. Suite 12<br>Moncton, NB E1C 4B7</div>
    <div class="row"><svg class="icon"><use href="#i-phone"/></svg>(506) 555-0147</div>
    <div class="row"><svg class="icon"><use href="#i-mail"/></svg>info@brennicksupply.ca</div>
    <div class="row"><svg class="icon"><use href="#i-web"/></svg>www.brennicksupply.ca</div>
  </div>
  <div class="socials"><span></span><span></span><span></span><span></span><span></span></div>
</section>

<!-- Presentation folder, closed -->
<section class="piece folder-front">
  <div class="edge"></div>
  <div class="wordmark">Brennick</div>
</section>
<section class="piece insert">
  <div class="line">418 Harbourline Rd.<br>Moncton, NB<br>(506) 555-0147<br>brennicksupply.ca</div>
  <div class="line" style="margin-top:60px">Supplies shipped across Canada</div>
  <div class="line">since 1969 from every warehouse</div>
  <div class="band"></div>
</section>

<!-- Presentation folder, open -->
<section class="piece folder-open">
  <div class="left"></div>
  <div class="right"></div>
  <svg width="131" height="243" viewBox="0 0 131 243">
    <path d="M0 243 V190 Q0 160 40 160 H131 V243 Z" fill="var(--red)"/>
  </svg>
</section>

<!-- Notepad cover -->
<section class="piece notebook">
  <div class="pattern" role="img" aria-label="Dark cover pattern of small repeated leaf shapes"></div>
  <div class="band"></div>
  <div class="spiral"><span></span><span></span><span></span><span></span><span></span><span></span><span></span><span></span><span></span><span></span><span></span><span></span><span></span><span></span><span></span><span></span><span></span><span></span><span></span><span></span></div>
  <div class="wordmark">Brennick</div>
</section>

</body>
</html>
```